Wholesale in Gold Jewellery & Gold Bullion

We are an established gold jewellery and gold bullion wholesaler selling these products to international clients. We already have a name and logo of our company, hence please view attached current card design. We need a completely new design to compliment our business and industry and the final design should be new and elegant.

Contact Information for Business Card

New card details must be same as per current card. Like logo, name, tel no. & etc.

Colors

Designer to choose colors to be used in the design.

```html
<!DOCTYPE html>
<html lang="en">
<head>
<meta charset="utf-8">
<title>Kaveri &amp; Co – Business Card</title>
<link rel="stylesheet" href="https://fonts.googleapis.com/css2?family=Montserrat:wght@400;500;600&display=swap">
<style>
  :root {
    --backdrop: #e9e9e7;
    --card: #ffffff;
    --gold: #e2ae3b;
    --ink: #3a2519;
    --text: #2b2b2b;
  }
  * { box-sizing: border-box; margin: 0; padding: 0; }
  html, body {
    width: 1200px; height: 900px; overflow: hidden;
    background: var(--backdrop);
    font-family: "Montserrat", Arial, sans-serif;
  }
  .business-card {
    position: absolute;
    left: 100px; top: 165px;
    width: 1000px; height: 570px;
    background: var(--card);
    box-shadow: 0 18px 40px rgba(0,0,0,0.16), 0 2px 6px rgba(0,0,0,0.08);
  }
  .brand {
    position: absolute;
    left: 250px; top: 92px;
    display: flex; align-items: center; gap: 28px;
  }
  .brand-dot {
    width: 118px; height: 118px; border-radius: 50%;
    background: var(--gold);
  }
  .brand-name {
    font-weight: 600; font-size: 34px; letter-spacing: 1px;
    color: var(--ink); margin-top: 70px;
  }
  .holder {
    position: absolute; left: 90px; top: 300px;
    text-align: right;
  }
  .holder-name {
    font-weight: 500; font-size: 40px; color: var(--ink); letter-spacing: 0.5px;
  }
  .holder-role {
    font-weight: 400; font-size: 30px; color: var(--gold); letter-spacing: 1px;
    margin-top: -2px;
  }
  .contact-list {
    position: absolute; left: 570px; top: 330px;
    list-style: none;
  }
  .contact-item {
    display: flex; align-items: center; gap: 22px;
    font-size: 24px; color: var(--text); height: 40px;
  }
  .contact-icon { width: 26px; height: 26px; flex: none; }
  .contact-icon * { fill: none; stroke: var(--gold); stroke-width: 2; }
  .contact-icon .solid { fill: var(--gold); stroke: none; }
  .address {
    position: absolute; left: 250px; top: 495px;
    font-size: 24px; color: var(--text); letter-spacing: 0.3px;
  }
</style>
</head>
<body>
  <section class="business-card">
    <div class="brand">
      <span class="brand-dot"></span>
      <span class="brand-name">KAVERI &amp; CO PTE LTD</span>
    </div>

    <div class="holder">
      <p class="holder-name">Rohan Devaraj</p>
      <p class="holder-role">Director</p>
    </div>

    <ul class="contact-list">
      <li class="contact-item">
        <svg class="contact-icon" viewBox="0 0 26 26" aria-hidden="true"><rect x="7" y="2" width="12" height="22" rx="2"/><line x1="11" y1="20" x2="15" y2="20"/></svg>
        +65 9123 4567
      </li>
      <li class="contact-item">
        <svg class="contact-icon" viewBox="0 0 26 26" aria-hidden="true"><path class="solid" d="M7 3l4 5-2.5 2.5c1.5 3 3.5 5 6.5 6.5L17.5 14.5l5 4-2.5 4C12 22 4 14 3.5 6z"/></svg>
        +65 6800 1200
      </li>
      <li class="contact-item">
        <svg class="contact-icon" viewBox="0 0 26 26" aria-hidden="true"><rect x="7" y="2" width="12" height="9"/><rect class="solid" x="2" y="11" width="22" height="11" rx="2"/></svg>
        +65 6800 1299
      </li>
      <li class="contact-item">
        <svg class="contact-icon" viewBox="0 0 26 26" aria-hidden="true"><rect class="solid" x="2" y="5" width="22" height="16"/><path d="M2 5l11 9 11-9" style="stroke:#fff"/></svg>
        rohan@kaverico.com
      </li>
    </ul>

    <p class="address">12 Amber Lane, Singapore 208815</p>
  </section>
</body>
</html>
```